Norvane Stationery Design Project

We need stationary design that goes with the attached logo. We have logo in two different versions. One in Red/Black and the other in Blue/Green. Red/Black is going to be our primary color and we are planning to use Blue/Green occasionally as necessary.

So we need stationary design in both color combinations. Maybe you can work with Red/Black first and once we decide on the design, then you can show the Blue/Green variation.

Please see the attached png and psd files for logo.

Target Market(s)

IT departments of Medium size Enterprises.

Industry/Entity Type

Work

Requirements
Must have
• -Letter head
-Cover page design for white papers and articles that are going to publish
-Business Card
-Envelope design
Nice to have
• - High level design template that we can follow for our internal web applications

```html
<!DOCTYPE html>
<html lang="en">
<head>
<meta charset="utf-8">
<title>Norvane Software – Business Card</title>
<link rel="stylesheet" href="https://fonts.googleapis.com/css2?family=Lato:wght@400;700;900&display=swap">
<style>
  :root {
    --stage: #2b2b2b;
    --card-white: #f7f7f7;
    --brand-red: #c8101a;
    --brand-red-dark: #9c0c14;
    --ink: #1a1a1a;
    --paper-text: #ffffff;
    --radius: 22px;
  }
  * { box-sizing: border-box; margin: 0; padding: 0; }
  html, body {
    width: 1200px; height: 997px; overflow: hidden;
    background: var(--stage);
    font-family: "Lato", Arial, sans-serif;
  }
  .stage { position: relative; width: 1200px; height: 997px; }

  .card {
    position: absolute;
    width: 540px; height: 308px;
    border-radius: var(--radius);
    overflow: hidden;
    background: var(--card-white);
    box-shadow: 0 18px 40px rgba(0,0,0,.45);
  }
  .card--front { left: 90px; top: 120px; }
  .card--back  { left: 570px; top: 520px; }

  .wordmark {
    display: flex; align-items: center; gap: 14px;
    color: var(--brand-red);
    font-weight: 900;
    font-size: 34px;
    letter-spacing: 4px;
    text-transform: uppercase;
    line-height: 1;
  }
  .wordmark__square {
    width: 30px; height: 30px; background: var(--brand-red); flex: none;
  }

  /* front */
  .front__top {
    height: 170px;
    display: flex; align-items: center; justify-content: center;
  }
  .front__stripes {
    height: 18px;
    background: repeating-linear-gradient(to bottom,
      var(--brand-red) 0 3px, #fff 3px 6px);
  }
  .front__band {
    height: 120px;
    background: linear-gradient(to bottom, var(--brand-red), var(--brand-red-dark));
    display: flex; align-items: center; justify-content: center;
  }
  .slogan {
    color: rgba(255,255,255,.85);
    font-size: 14px; letter-spacing: 4px;
    text-transform: uppercase;
  }

  /* back */
  .back__logo-side {
    position: absolute; left: 0; top: 0; bottom: 0; width: 270px;
    display: flex; align-items: center; justify-content: center;
  }
  .back__logo-side .wordmark { font-size: 24px; letter-spacing: 3px; gap: 10px; }
  .back__logo-side .wordmark__square { width: 22px; height: 22px; }
  .back__divider {
    position: absolute; left: 270px; top: 0; bottom: 0; width: 20px;
    background: linear-gradient(to right,
      var(--brand-red) 0 3px, #fff 3px 7px, var(--brand-red) 7px 10px, #fff 10px 14px, var(--brand-red) 14px);
  }
  .back__info {
    position: absolute; left: 290px; right: 0; top: 0; bottom: 0;
    background: linear-gradient(135deg, var(--brand-red), var(--brand-red-dark));
    padding: 34px 26px;
    color: var(--paper-text);
  }
  .person__name { color: var(--ink); font-weight: 900; font-size: 22px; }
  .person__title { font-size: 12px; font-weight: 700; letter-spacing: 1px; margin-top: 4px; }
  .contact-list { list-style: none; margin-top: 70px; }
  .contact-list li {
    display: flex; align-items: center; gap: 10px;
    font-size: 13.5px; margin-bottom: 8px;
  }
  .contact-list svg { width: 14px; height: 14px; fill: var(--ink); flex: none; }
</style>
</head>
<body>
<main class="stage">

  <section class="card card--front" aria-label="Business card front">
    <div class="front__top">
      <div class="wordmark"><span class="wordmark__square"></span>Norvane Software</div>
    </div>
    <div class="front__stripes"></div>
    <div class="front__band">
      <p class="slogan">Your Slogan / Tagline Here</p>
    </div>
  </section>

  <section class="card card--back" aria-label="Business card back">
    <div class="back__logo-side">
      <div class="wordmark"><span class="wordmark__square"></span>Norvane</div>
    </div>
    <div class="back__divider"></div>
    <div class="back__info">
      <h1 class="person__name">Dana Holt</h1>
      <p class="person__title">FOUNDER/CEO</p>
      <ul class="contact-list">
        <li>
          <svg viewBox="0 0 16 16" aria-hidden="true"><path d="M3 1h3l1 4-2 1a9 9 0 0 0 5 5l1-2 4 1v3c0 1-1 2-2 2A13 13 0 0 1 1 3c0-1 1-2 2-2z"/></svg>
          555 210 4830
        </li>
        <li>
          <svg viewBox="0 0 16 16" aria-hidden="true"><path d="M4 1h7v4H4zM2 6h12v7h-2v2H4v-2H2zm3 5v3h6v-3z"/></svg>
          555 210 4800
        </li>
        <li>
          <svg viewBox="0 0 16 16" aria-hidden="true"><path d="M1 3h14v10H1zm1 1 6 5 6-5z"/></svg>
          info@norvanesoftware.com
        </li>
        <li>
          <svg viewBox="0 0 16 16" aria-hidden="true"><path d="M6 10l4-4 1 1-4 4zM3 9l2-2 1 1-2 2 2 2 2-2 1 1-2 2a2 2 0 0 1-3 0L3 12a2 2 0 0 1 0-3zm10-2-2 2-1-1 2-2-2-2-2 2-1-1 2-2a2 2 0 0 1 3 0l1 1a2 2 0 0 1 0 3z"/></svg>
          www.norvanesoftware.com
        </li>
      </ul>
    </div>
  </section>

</main>
</body>
</html>
```